HOT TUB - SPAS service needs an business card

I need an business for my company who his specialise in a maintenance,water treatment and cleaning of Hot Tub - Spas for commercial and residential customers. The company operate mainly in the ski resort of Chamonix, Megève and St Gervais. The final product should communicate pure water, cleanest and professional for luxury property's.
I have upload a logo but any improvement on it is welcome.(color,size, details etc..) or any other idea. Thank you
Company Name: 58 BAINS
My name: Lucien Marchetti
Email: lucimarch@examplemail.net
Tel: +33 (0)6 71 58 29 64
Description to be on the card in french(first langage) and in English:
- Spas service
- Entretien, traitement eau, nettoyage.
- Maintenance, water treatment, cleaning.
Industry/Entity Type
Residential
Colors
Designer to choose colors to be used in the design.
Look and feel
Each slider illustrates characteristics of the customer's brand and the style your logo design should communicate.

```html
<!DOCTYPE html>
<html lang="fr">
<head>
<meta charset="utf-8">
<title>58 BAINS – Cartes de visite</title>
<link rel="stylesheet" href="https://fonts.googleapis.com/css2?family=Source+Sans+3:wght@400;600;700&display=swap">
<style>
  :root {
    --backdrop: #b98152;
    --card-blue: #21a4f7;
    --deep-blue: #0b74d4;
    --mid-blue: #3fb2f8;
    --swoosh-grey: #d6d9dc;
    --art-tone: #5dbcf9;
    --ink-white: #ffffff;
  }
  * { box-sizing: border-box; margin: 0; padding: 0; }
  html, body {
    width: 1200px; height: 986px; overflow: hidden;
    background: var(--backdrop);
    font-family: "Source Sans 3", "Myriad Pro", sans-serif;
    color: var(--ink-white);
  }
  .stage { position: relative; width: 1200px; height: 986px; }
  .card {
    position: absolute; width: 783px; height: 446px;
    background: var(--card-blue); overflow: hidden;
    box-shadow: 0 3px 8px rgba(0,0,0,0.25);
  }
  .card--front { left: 375px; top: 41px; }
  .card--back  { left: 39px;  top: 503px; }

  .brand-art {
    position: absolute;
    background: linear-gradient(180deg, var(--card-blue) 0%, var(--art-tone) 100%);
    border-bottom: 2px solid rgba(255,255,255,0.85);
  }
  .card--front .brand-art { left: 147px; top: 23px; width: 500px; height: 137px; }
  .card--back  .brand-art { left: 97px;  top: 86px; width: 604px; height: 166px; }

  .centered { position: absolute; left: 0; width: 100%; text-align: center; white-space: nowrap; }
  .company-name { top: 164px; font-size: 38px; font-weight: 600; letter-spacing: 0.5px; }
  .person-name  { top: 249px; font-size: 34px; font-weight: 700; }
  .contact { font-size: 27px; font-weight: 600; display: flex; justify-content: center; align-items: center; gap: 10px; }
  .contact--phone { top: 296px; }
  .contact--email { top: 333px; font-weight: 400; }
  .contact svg { width: 22px; height: 22px; flex: none; }

  .wave { position: absolute; left: 0; bottom: 0; width: 783px; height: 446px; }

  .service-title { top: 310px; font-size: 30px; font-weight: 600; }
  .service-line  { font-size: 29px; font-weight: 400; }
  .service-line--fr { top: 356px; left: 0; }
  .service-line--en { top: 393px; left: -8px; }
</style>
</head>
<body>
<main class="stage">

  <section class="card card--front">
    <svg class="wave" viewBox="0 0 783 446" aria-hidden="true">
      <path fill="var(--swoosh-grey)" d="M0,345 C60,392 150,418 300,420 C450,421 620,414 783,428 L783,433 C720,425 640,427 520,436 C340,450 140,448 0,392Z"/>
      <path fill="var(--mid-blue)" d="M0,392 C140,448 340,450 520,436 C640,427 720,425 783,433 L783,438 C720,432 640,434 520,442 C340,455 140,452 0,400Z"/>
      <path fill="var(--deep-blue)" d="M0,400 C140,452 340,455 520,442 C640,434 720,432 783,438 L783,446 L0,446Z"/>
    </svg>
    <div class="brand-art" role="img" aria-label="Line illustration of mountains, a chalet and a hot tub"></div>
    <p class="centered company-name">58 BAINS</p>
    <p class="centered person-name">Lucien Marchetti</p>
    <p class="centered contact contact--phone">
      <svg viewBox="0 0 24 24" aria-hidden="true"><circle cx="12" cy="12" r="10" fill="none" stroke="#fff" stroke-width="1.6"/><path d="M8.5 7 L10.5 7 L11 9.5 L9.8 10.4 C10.5 12 12 13.5 13.6 14.2 L14.5 13 L17 13.5 L17 15.5 C17 16.3 16.3 17 15.5 17 C11 16.6 7.4 13 7 8.5 C7 7.7 7.7 7 8.5 7Z" fill="#fff"/></svg>
      +33 (0)6 71 58 29 64
    </p>
    <p class="centered contact contact--email">
      <svg viewBox="0 0 24 24" aria-hidden="true"><path d="M2 10 L12 4 L22 10 L22 20 L2 20Z" fill="#fff"/><path d="M2 10 L12 16 L22 10" fill="none" stroke="var(--card-blue)" stroke-width="1.6"/></svg>
      lucimarch@examplemail.net
    </p>
  </section>

  <section class="card card--back">
    <div class="brand-art" role="img" aria-label="Line illustration of mountains, a chalet and a hot tub"></div>
    <p class="centered service-title">SPAS SERVICES</p>
    <p class="centered service-line service-line--fr">• Entretien &nbsp;• traitement eau &nbsp;• nettoyage</p>
    <p class="centered service-line service-line--en">• Maintenance &nbsp;• water treatment &nbsp;• cleaning.</p>
  </section>

</main>
</body>
</html>
```